BUSINESS CARD DESIGN

NAME- DALE VORSKIN
PHONE NUMER - 555- 714-9082
EMAIL- OFFICE@TRV-GROUNDMAKRZ.COM
BACK OF CARD- SPEACIALIZES IN LAND CLEARING, FORESTRY MUCLHING AND EXCAVATION

Contact Information for Business Card

NAME- DALE VORSKIN PHONE NUMER - 555- 714-9082 EMAIL- OFFICE@TRV-GROUNDMAKRZ.COM BACK OF CARD- SPEACIALIZES IN LAND CLEARING , MUCLHING AND EXCAVATION

```html
<!DOCTYPE html>
<html lang="en">
<head>
<meta charset="utf-8">
<title>Traverse Groundmakrz LLC – Business Card</title>
<link rel="stylesheet" href="https://fonts.googleapis.com/css2?family=Montserrat:wght@400;500;700&display=swap">
<style>
  :root {
    --backdrop: #6e5a44;
    --card-white: #ffffff;
    --card-black: #060606;
    --gold: #f2b705;
    --ink: #111111;
    --text: #1c1c1c;
  }
  * { box-sizing: border-box; margin: 0; padding: 0; }
  html, body { width: 900px; height: 1200px; overflow: hidden; }
  body {
    background: var(--backdrop);
    font-family: "Montserrat", Arial, sans-serif;
    position: relative;
  }
  .card {
    position: absolute;
    width: 742px;
    height: 442px;
    border-radius: 24px;
    overflow: hidden;
  }
  .card-front { left: 80px; top: 130px; background: var(--card-white); }
  .card-back  { left: 78px; top: 638px; background: var(--card-black); }

  .brand {
    position: absolute;
    display: flex;
    flex-direction: column;
    align-items: center;
    text-align: center;
  }
  .brand-dot {
    width: 110px; height: 110px;
    border-radius: 50%;
    border: 6px solid currentColor;
  }
  .brand-name {
    font-weight: 700;
    letter-spacing: 2px;
    line-height: 1.25;
  }
  .brand-phone {
    font-weight: 700;
    letter-spacing: 6px;
  }
  .card-front .brand { left: 50px; top: 26px; width: 245px; color: var(--ink); }
  .card-front .brand-dot { margin-bottom: 12px; }
  .card-front .brand-name { font-size: 18px; }
  .card-front .brand-phone { font-size: 12px; margin-top: 6px; }

  .card-back .brand { left: 0; right: 0; top: 66px; color: var(--gold); }
  .card-back .brand-dot { width: 150px; height: 150px; border-width: 8px; margin-bottom: 18px; }
  .card-back .brand-name { font-size: 30px; }
  .card-back .brand-phone { font-size: 16px; letter-spacing: 9px; margin-top: 10px; }
  .specialty {
    margin-top: 18px;
    font-size: 13px;
    font-weight: 500;
    letter-spacing: 1.5px;
    text-transform: uppercase;
    color: var(--gold);
  }

  .holder {
    position: absolute;
    right: 52px; top: 64px;
    text-align: right;
  }
  .holder-name { color: var(--gold); font-weight: 700; font-size: 24px; letter-spacing: 0.5px; }
  .holder-role { color: var(--text); font-size: 15px; font-weight: 500; margin-top: 6px; }

  .contact-list {
    position: absolute;
    left: 44px; top: 323px;
    list-style: none;
  }
  .contact-list li {
    display: flex; align-items: center; gap: 8px;
    font-size: 15.5px; color: var(--text);
    height: 28px;
  }
  .contact-list svg { width: 16px; height: 16px; fill: var(--gold); flex: none; }

  .brand-mark-large {
    position: absolute;
    left: 405px; top: 140px;
    width: 325px; height: 295px;
    display: flex; align-items: center; justify-content: center;
  }
  .brand-mark-large .brand-dot {
    width: 280px; height: 280px;
    border: 14px solid var(--ink);
  }
</style>
</head>
<body>
  <section class="card card-front">
    <div class="brand">
      <span class="brand-dot"></span>
      <span class="brand-name">TRAVERSE GROUNDMAKRZ LLC</span>
      <span class="brand-phone">555-714-9082</span>
    </div>

    <div class="holder">
      <div class="holder-name">DALE VORSKIN</div>
      <div class="holder-role">Managing Director</div>
    </div>

    <ul class="contact-list">
      <li>
        <svg viewBox="0 0 16 16" aria-hidden="true"><path d="M3.6 1.5l2.3 2.6-1.4 1.8a9 9 0 0 0 5.6 5.6l1.8-1.4 2.6 2.3-1.6 2.1C7.3 14 2 8.7 1.5 3.1z"/></svg>
        555- 714-9082
      </li>
      <li>
        <svg viewBox="0 0 16 16" aria-hidden="true"><path d="M1 3.5h14v1.4L8 9.3 1 4.9z"/><path d="M1 6.6l7 4.4 7-4.4v5.9H1z"/></svg>
        OFFICE@TRV-GROUNDMAKRZ.COM
      </li>
      <li>
        <svg viewBox="0 0 16 16" aria-hidden="true"><circle cx="8" cy="8" r="7"/><path d="M1 8h14M8 1c-3 3.5-3 10.5 0 14M8 1c3 3.5 3 10.5 0 14" fill="none" stroke="#fff" stroke-width="1"/></svg>
        WWW.TRV-GROUNDMAKRZ.COM
      </li>
    </ul>

    <div class="brand-mark-large" aria-hidden="true">
      <span class="brand-dot"></span>
    </div>
  </section>

  <section class="card card-back">
    <div class="brand">
      <span class="brand-dot"></span>
      <span class="brand-name">TRAVERSE GROUNDMAKRZ LLC</span>
      <span class="brand-phone">555-714-9082</span>
      <p class="specialty">Specializes in land clearing, forestry mulching and excavation</p>
    </div>
  </section>
</body>
</html>
```